Broschüre für Anbieter von Haushaltshilfen und Alltagsbegleitern für Privathaushalte
Zielgruppe
Wir bieten Haushaltshilfen und Alltagsbegleiter für Privathaushalte an. Unsere Hauptkundenklientel sind Pflegebedürftige Menschen denen eine Haushaltshilfe von der Pflegekasse zusteht. Weitere Kunden sind Familien und/oder Singlehaushalte, die eine Haushaltfshilfe benötigen.
Aufgabenstellung
- Das Prospekt sollte DIN A4 sein, sind aber auch offen für andere Formate
- Farbdesign muß unsere Logofarben enthalten
- In dem Prospekt müßen unsere Leistungen wie auf unserer Internetseite www.wolkenmut.de beschrieben sein.
- Seitenanzahl insgesamt 4 Seiten

```html
<!DOCTYPE html>
<html lang="de">
<head>
<meta charset="utf-8">
<title>Wolkenmut – Broschüre</title>
<link href="https://fonts.googleapis.com/css2?family=Cinzel:wght@500;700&family=Roboto:ital,wght@0,400;0,500;0,700;1,500&display=swap" rel="stylesheet">
<style>
  :root{
    --bg:#e4e4e4;
    --red:#b3141d;
    --teal:#62c6cc;
    --teal-dark:#52a7ac;
    --teal-text:#3fb3ba;
    --ink:#2b2b2b;
    --page-grey-a:#ececed;
    --page-grey-b:#d6d7d8;
    --white:#ffffff;
  }
  *{box-sizing:border-box;margin:0;padding:0}
  html,body{width:1200px;height:900px;overflow:hidden;background:var(--bg)}
  body{position:relative;font-family:"Roboto",Arial,sans-serif;color:var(--ink)}

  .spread{position:absolute;left:200px;width:800px;height:413px;overflow:hidden;box-shadow:0 8px 22px rgba(0,0,0,.18)}
  .spread--inside{top:28px}
  .spread--outside{top:462px}
  .page{position:absolute;top:0;width:400px;height:413px}
  .page--left{left:0}
  .page--right{left:400px}
  .page--grey{background:linear-gradient(135deg,var(--page-grey-a),var(--page-grey-b))}
  .page--white{background:var(--white)}
  .abs{position:absolute}

  .display{font-family:"Cinzel",Georgia,serif;color:var(--red);font-weight:700;line-height:1.15}
  .label-caps{font-family:"Cinzel",Georgia,serif;color:var(--red);font-weight:500;letter-spacing:.06em}

  /* inside, left page */
  .inside-title{left:29px;top:26px;font-size:21px}
  .intro{left:29px;top:94px;width:290px;font-size:9.6px;line-height:1.3}
  .intro em{color:var(--red);font-style:italic;font-weight:500}
  .intro--cta{top:145px;width:200px}
  .services-title{left:29px;top:188px;font-size:12.5px}
  .links{left:0;top:0;width:400px;height:413px}
  .service{position:absolute;width:59px;height:59px;margin-left:-29.5px;margin-top:-29.5px;border-radius:50%;border:1.4px solid var(--teal);background:#f1f2f2}
  .service-art{position:absolute;inset:8px;border-radius:50%;background:radial-gradient(circle,#c9cbcc,#e6e7e7)}
  .service-name{position:absolute;transform:translateX(-50%);font-size:6.6px;font-weight:700;color:var(--teal-text);letter-spacing:.04em;white-space:nowrap}

  .call-circle{left:236px;top:146px;width:156px;height:156px;border-radius:50%;background:var(--teal-dark);color:var(--white);text-align:center;padding-top:32px;font-size:11px;line-height:1.25;z-index:3}
  .call-circle b{display:block;font-weight:700;letter-spacing:.06em;margin-top:6px}
  .call-circle b:first-child{margin-top:0}
  .call-circle span{display:block;letter-spacing:.03em}

  .photo-cleaning{left:380px;top:166px;width:272px;height:272px;border-radius:50%;background:radial-gradient(circle at 60% 40%,#f3efe8,#d8d2c8 55%,#b9b4ad);z-index:2}

  /* inside, right page */
  .lead{left:428px;top:40px;width:146px;font-size:6.3px;line-height:1.4;color:#333}
  .lead em{color:var(--red);font-weight:500}
  .lead p+p{margin-top:9px}
  .benefits{left:594px;top:0;width:206px;height:413px;background:var(--teal);z-index:4;color:var(--white);text-align:center}
  .benefits-title{font-family:"Cinzel",Georgia,serif;font-weight:500;font-size:11.5px;letter-spacing:.1em;margin-top:28px}
  .benefit{position:absolute;left:0;width:206px}
  .benefit svg{display:block;margin:0 auto}
  .benefit p{font-size:6.2px;font-weight:700;line-height:1.3;margin-top:6px;padding:0 14px}

  /* outside, left page */
  .contact{left:26px;top:120px}
  .contact dt{font-family:"Cinzel",Georgia,serif;color:var(--red);font-size:12px;letter-spacing:.06em;line-height:1}
  .contact dd{font-size:10.5px;font-weight:500;margin-bottom:14px;margin-top:2px;letter-spacing:.02em}
  .contact dd small{display:block;font-size:9.5px;font-weight:400}
  .cta{right:430px;top:110px;text-align:right;font-family:"Cinzel",Georgia,serif;color:var(--teal-text);font-size:25px;line-height:1.17;font-weight:500;z-index:2}
  .cta-line{left:256px;top:210px;width:246px;height:2px;background:var(--teal-text);z-index:2}
  .footer-brand{left:26px;top:366px;display:flex;align-items:center;gap:6px}
  .brand-dot{width:20px;height:20px;border-radius:50%;background:var(--red)}
  .brand-name{font-family:"Cinzel",Georgia,serif;color:var(--red);font-weight:700;font-size:13px;letter-spacing:.02em}
  .footer-info{top:370px;font-size:6.8px;line-height:1.45;color:#333}

  /* outside, right page */
  .tagline{left:428px;top:27px;font-size:7.6px;letter-spacing:.06em;text-transform:uppercase;color:#333}
  .cover-title{left:427px;top:42px;width:360px;font-size:18.5px}
  .photo-together{left:539px;top:107px;width:304px;height:304px;border-radius:50%;background:radial-gradient(circle at 45% 45%,#d8b85a,#a78a62 45%,#6d6a64 80%)}
  .cover-brand{left:425px;top:312px;width:82px;text-align:center}
  .cover-brand .brand-dot{width:34px;height:34px;margin:0 auto 6px}
</style>
</head>
<body>

<section class="spread spread--inside" aria-label="Innenseiten">
  <div class="page page--left page--grey">
    <h1 class="abs display inside-title">Verschenken Sie<br>nicht Ihr Geld!</h1>
    <p class="abs intro">Den Alltag zu bewältigen kann eine echte Herausforderung sein. Egal, ob Sie Hilfe beim Einkaufen oder anderen alltäglichen Aktivitäten benötigen, <em>wir helfen gerne.</em></p>
    <p class="abs intro intro--cta">Buchen Sie gleich Ihren kostenlosen Beratungstermin und informieren Sie sich!</p>
    <h2 class="abs label-caps services-title">Unsere Leistungen</h2>

    <svg class="abs links" viewBox="0 0 400 413" aria-hidden="true">
      <g stroke="#c0424a" stroke-width=".8" stroke-dasharray="1.5 2" fill="none">
        <line x1="74" y1="280" x2="82" y2="300"/>
        <line x1="118" y1="306" x2="140" y2="286"/>
        <line x1="178" y1="290" x2="186" y2="310"/>
        <line x1="236" y1="330" x2="249" y2="322"/>
        <line x1="306" y1="318" x2="322" y2="332"/>
      </g>
    </svg>

    <div class="service" style="left:60px;top:242px"><div class="service-art" role="img" aria-label="Zeichnung eines Staubsaugers"></div></div>
    <span class="service-name" style="left:60px;top:276px">HAUSHALTSHILFE</span>
    <div class="service" style="left:161px;top:256px"><div class="service-art" role="img" aria-label="Zeichnung einer Einkaufstüte"></div></div>
    <span class="service-name" style="left:161px;top:289px">EINKAUFSHILFE</span>
    <div class="service" style="left:98px;top:326px"><div class="service-art" role="img" aria-label="Zeichnung eines Besens"></div></div>
    <span class="service-name" style="left:98px;top:360px">KEHRWOCHE</span>
    <div class="service" style="left:203px;top:337px"><div class="service-art" role="img" aria-label="Zeichnung von Reinigungsmitteln"></div></div>
    <span class="service-name" style="left:203px;top:371px">FENSTERREINIGUNG</span>
    <div class="service" style="left:277px;top:308px;z-index:4"><div class="service-art" role="img" aria-label="Zeichnung einer Waschmaschine"></div></div>
    <span class="service-name" style="left:277px;top:342px">WÄSCHESERVICE</span>
    <div class="service" style="left:350px;top:347px;z-index:4"><div class="service-art" role="img" aria-label="Zeichnung eines Herzens mit Signalwellen"></div></div>
    <span class="service-name" style="left:350px;top:380px;z-index:4">ALLTAGSBEGLEITUNG</span>
  </div>

  <div class="page page--right page--white"></div>

  <div class="abs photo-cleaning" role="img" aria-label="Foto: Person saugt Staub unter einem Teppich in heller Wohnung"></div>

  <div class="abs call-circle">
    <b>TELEFON:</b><span>0711 23 45 67 80</span>
    <b>MOBIL:</b><span>0170 98 76 54 32</span><span>(24/7 erreichbar)</span>
  </div>

  <div class="abs lead">
    <p><em>Um Älteren oder beeinträchtigten Menschen</em> ein Leben in ihrem sozialen Umfeld zu ermöglichen, bedarf es der Unterstützung im Alltag. Die dabei täglich anfallenden Aufgaben des Haushalts können oft belastend sein und die Pflege der betroffenen Personen erschweren.</p>
    <p>Um sie zu entlasten, bieten wir Ihnen <em>bedarfsorientierte Hilfe</em> rund um den Haushalt an. Mit unserem breiten Spektrum an Services möchten wir Sie beim bewältigen des Alltags unterstützen.</p>
  </div>

  <aside class="abs benefits">
    <h2 class="benefits-title">UNSERE VORTEILE</h2>
    <div class="benefit" style="top:76px">
      <svg width="34" height="44" viewBox="0 0 34 44" fill="none" stroke="#1d2b2c" stroke-width="1.6"><path d="M2 2h22l8 8v32H2z"/><path d="M24 2v8h8"/><path d="M20 16a6 6 0 1 0 0 10M12 19h8M12 23h8"/><path d="M8 32h18M8 36h18"/></svg>
      <p>Abrechnung mit allen<br>Pflegekassen möglich</p>
    </div>
    <div class="benefit" style="top:164px">
      <svg width="54" height="44" viewBox="0 0 54 44" fill="none" stroke="#1d2b2c" stroke-width="1.6"><path d="M24 2h6v7h7v6h-7v7h-6v-7h-7V9h7z"/><path d="M2 30l8-6c4-3 8-2 12 0h10a3 3 0 0 1 0 6H22"/><path d="M32 28l12-7a3 3 0 0 1 4 4L34 37H14l-6 4"/></svg>
      <p>Abrechnung über den Entlastungsbetrag von<br>mind. 125€ mtl. ab Pflegegrad 1 möglich</p>
    </div>
    <div class="benefit" style="top:254px">
      <svg width="54" height="44" viewBox="0 0 54 44" fill="none" stroke="#1d2b2c" stroke-width="1.6"><path d="M27 22S16 15 16 8a5.5 5.5 0 0 1 11-1 5.5 5.5 0 0 1 11 1c0 7-11 14-11 14z"/><path d="M2 32l8-6c4-3 8-2 12 0h10a3 3 0 0 1 0 6H22"/><path d="M32 30l12-7a3 3 0 0 1 4 4L34 39H14l-6 4"/></svg>
      <p>auch über die<br>Verhinderungspflege</p>
    </div>
    <div class="benefit" style="top:344px">
      <svg width="44" height="44" viewBox="0 0 44 44" fill="none" stroke="#1d2b2c" stroke-width="1.6"><path d="M2 2h22l6 6v34H2z"/><path d="M7 12h16M7 18h18M7 24h14M7 30h10"/><path d="M38 14l4 4-16 16-6 2 2-6z"/></svg>
      <p>Hilfe bei der Antragstellung</p>
    </div>
  </aside>
</section>

<section class="spread spread--outside" aria-label="Außenseiten">
  <div class="page page--left page--white">
    <dl class="abs contact">
      <dt>TELEFON:</dt><dd>0711 23 45 67 80</dd>
      <dt>MOBIL:</dt><dd>0170 98 76 54 32<small>(24/7 erreichbar)</small></dd>
      <dt>E-MAIL:</dt><dd>info@wolkenmut.de</dd>
      <dt>WEBSITE:</dt><dd>www.wolkenmut.de</dd>
    </dl>
    <div class="abs footer-brand"><span class="brand-dot"></span><span class="brand-name">WOLKENMUT</span></div>
    <p class="abs footer-info" style="left:170px">Lindenweg 8<br>73000 Beispielstadt</p>
    <p class="abs footer-info" style="left:251px">0711 23456780<br>info@wolkenmut.de</p>
  </div>

  <div class="page page--right page--grey"></div>

  <p class="abs cta">Jetzt<br>beraten<br>lassen</p>
  <div class="abs cta-line"></div>

  <p class="abs tagline">Wolkenmut Haushaltshilfen und Alltagsbegleiter</p>
  <h1 class="abs display cover-title">Wir sind Ihr Halt, wenn der<br>Alltag schwierig wird</h1>
  <div class="abs photo-together" role="img" aria-label="Foto: ältere Dame und junge Begleiterin gehen lachend mit Einkaufstüte durch die Stadt"></div>
  <div class="abs cover-brand"><div class="brand-dot"></div><span class="brand-name">WOLKENMUT</span></div>
</section>

</body>
</html>
```